Animal Eye Clinic needs a Business card

We are a new veterinary ophthalmology practice (Ridgeline Pet Vision Care) and we need a business card designed. We only see animal eyes - we are not a regular veterinary clinic. We already have a logo. We are looking for a professional, good looking business card to hand out to our clients. We are looking for something simple but professional and contemporary. Our logo is likely the only picture/graphic that needs to be on the card.
Updates

Contact Information for Business Card

Delia Vossman, BSc, DVM, MSc, DipACVO
Veterinary Ophthalmologist

Phone: 250.418.3927
Email: ridgelinepetvisioncare@mailbox-example.net
Website: ridgelinepetvisioncare-example.net
Address: 1874 Thornbury Rd
Kelowna, BC, V1X 4M9

Colors

Designer to choose colors to be used in the design.

Requirements
Must have
• Our logo (attached)

```html
<!DOCTYPE html>
<html lang="en">
<head>
<meta charset="utf-8">
<title>Ridgeline Pet Vision Care – Business Card</title>
<link href="https://fonts.googleapis.com/css2?family=Exo+2:wght@700;800&family=Roboto+Condensed:wght@400;600&display=swap" rel="stylesheet">
<style>
  :root {
    --backdrop: #2b2b2b;
    --teal: #1d9aa8;
    --teal-soft: #33a7b3;
    --paper: #ffffff;
    --ink-grey: #6d6d6d;
    --body-font: "Roboto Condensed", Arial, sans-serif;
    --name-font: "Exo 2", Arial, sans-serif;
  }
  * { box-sizing: border-box; margin: 0; padding: 0; }
  html, body { width: 1200px; height: 900px; overflow: hidden; background: var(--backdrop); }
  .canvas { position: relative; width: 1200px; height: 900px; }

  .card {
    position: absolute;
    left: 260px;
    width: 680px;
    height: 388px;
    box-shadow: 0 10px 28px rgba(0,0,0,.45);
  }

  /* Front */
  .card--front {
    top: 50px;
    background: var(--teal);
    display: flex;
    align-items: center;
    justify-content: center;
    gap: 22px;
  }
  .front-mark {
    width: 96px; height: 96px;
    border-radius: 50%;
    background: var(--paper);
  }
  .front-name {
    font-family: var(--body-font);
    font-weight: 600;
    font-size: 34px;
    color: var(--paper);
    line-height: 1.15;
    max-width: 300px;
  }

  /* Back */
  .card--back {
    top: 462px;
    background: var(--paper);
    display: flex;
    align-items: center;
    padding: 0 24px 0 38px;
  }
  .brand {
    display: flex;
    align-items: center;
    gap: 14px;
    width: 262px;
  }
  .brand-mark {
    flex: none;
    width: 52px; height: 52px;
    border-radius: 50%;
    background: var(--teal);
  }
  .brand-name {
    font-family: var(--body-font);
    font-weight: 600;
    font-size: 23px;
    line-height: 1.12;
    color: var(--teal);
  }
  .divider {
    width: 2px;
    height: 196px;
    background: var(--teal);
    margin: 0 18px 0 10px;
  }
  .contact { font-family: var(--body-font); color: var(--ink-grey); }
  .contact-name {
    font-family: var(--name-font);
    font-weight: 800;
    font-size: 31px;
    letter-spacing: .5px;
    color: var(--teal);
    line-height: 1;
  }
  .credentials {
    font-family: var(--name-font);
    font-weight: 700;
    font-size: 15px;
    color: var(--teal);
    margin-top: 3px;
  }
  .role, .address { font-size: 16px; line-height: 1.35; }
  .address { margin-top: 4px; }
  .contact-list { list-style: none; margin-top: 8px; }
  .contact-list li {
    display: flex; align-items: center; gap: 7px;
    font-size: 15px; line-height: 1.5;
  }
  .contact-list svg { flex: none; width: 15px; height: 15px; }
</style>
</head>
<body>
<div class="canvas">

  <section class="card card--front" aria-label="Card front">
    <div class="front-mark"></div>
    <div class="front-name">Ridgeline Pet Vision Care</div>
  </section>

  <section class="card card--back" aria-label="Card back">
    <div class="brand">
      <div class="brand-mark"></div>
      <div class="brand-name">Ridgeline Pet Vision Care</div>
    </div>
    <div class="divider"></div>
    <div class="contact">
      <h1 class="contact-name">DELIA VOSSMAN</h1>
      <p class="credentials">BSc, DVM, MSc, DipACVO</p>
      <p class="role">Veterinary Ophthalmologist</p>
      <p class="address">1874 Thornbury Rd, Kelowna, BC, V1X 4M9</p>
      <ul class="contact-list">
        <li>
          <svg viewBox="0 0 16 16" fill="none" stroke="#1d9aa8" stroke-width="1.4"><circle cx="8" cy="8" r="6.8"/><path d="M5.6 4.6l1.3 1.6-.8 1c.5 1 1.2 1.7 2.2 2.2l1-.8 1.6 1.3-.8 1.2c-2.6-.3-5.2-2.9-5.5-5.5z" fill="#1d9aa8" stroke="none"/></svg>
          250.418.3927
        </li>
        <li>
          <svg viewBox="0 0 16 16" fill="none" stroke="#1d9aa8" stroke-width="1.4"><rect x="1.5" y="3.5" width="13" height="9"/><path d="M1.5 3.5L8 9l6.5-5.5"/></svg>
          ridgelinepetvisioncare@mailbox-example.net
        </li>
        <li>
          <svg viewBox="0 0 16 16" fill="none" stroke="#1d9aa8" stroke-width="1.3"><circle cx="8" cy="8" r="6.5"/><ellipse cx="8" cy="8" rx="3" ry="6.5"/><path d="M1.5 8h13M2.5 5h11M2.5 11h11"/></svg>
          www.ridgelinepetvisioncare-example.net
        </li>
      </ul>
    </div>
  </section>

</div>
</body>
</html>
```